Construction Company

Design a clutter free business card, it can be double-sided utilizing the logo for VKM Ltd simple with all relevant contact information.

Please also a letterhead design to function for the purposes of invoicing, all mail requirements, with header to be distinctive while the footer ties page together and incorporates all necessary information.

For now, please use generic / dummy text and when a winner is selected, I will disclose the contact information.

Hi Designers! Please read the updated brief which includes the design of a business card and letterhead. Thank you!

```html
<!DOCTYPE html>
<html lang="en">
<head>
<meta charset="utf-8">
<title>VKM Ltd Business Card</title>
<link rel="stylesheet" href="https://fonts.googleapis.com/css2?family=Roboto:wght@400;500&display=swap">
<style>
  :root {
    --stage: #3a3a3a;
    --stage-edge: #1f1f1f;
    --card-light: #ffffff;
    --card-dark: #050505;
    --brand-blue: #0d3a9c;
    --brand-gold: #b8961f;
    --faint-grey: #ececec;
    --text-light: #ffffff;
  }
  * { box-sizing: border-box; margin: 0; padding: 0; }
  html, body { width: 1200px; height: 901px; overflow: hidden; }
  body {
    background: radial-gradient(ellipse at 60% 25%, var(--stage), var(--stage-edge));
    font-family: "Roboto", Arial, sans-serif;
    position: relative;
  }
  .card {
    position: absolute;
    left: 250px;
    width: 700px;
    height: 400px;
    overflow: hidden;
    box-shadow: 0 12px 30px rgba(0,0,0,0.5);
  }
  .card--front { top: 30px; background: var(--card-light); }
  .card--back { top: 470px; background: var(--card-dark); }

  .wordmark {
    position: absolute;
    font-weight: 500;
    color: var(--brand-blue);
    letter-spacing: 2px;
    white-space: nowrap;
  }
  .card--front .wordmark { left: 150px; top: 150px; font-size: 72px; }
  .card--back .wordmark { left: 50px; top: 36px; font-size: 64px; }

  .front-accent {
    position: absolute;
    right: -110px;
    top: 60px;
    width: 300px;
    height: 300px;
    border-radius: 50%;
    background: var(--faint-grey);
  }
  .back-accent {
    position: absolute;
    right: -150px;
    top: 90px;
    width: 300px;
    height: 300px;
    border-radius: 50%;
    background: var(--brand-gold);
  }

  .holder { position: absolute; left: 50px; top: 140px; }
  .holder__name { color: var(--brand-blue); font-size: 30px; font-weight: 500; }
  .holder__role { color: var(--text-light); font-size: 19px; margin-top: 2px; }

  .contact { position: absolute; left: 50px; top: 238px; list-style: none; }
  .contact__item {
    display: flex; align-items: center; gap: 12px;
    color: var(--text-light); font-size: 21px; line-height: 32px;
  }
  .contact__icon { width: 18px; height: 18px; flex: none; }
  .contact__address { color: var(--text-light); font-size: 21px; line-height: 32px; }
</style>
</head>
<body>
  <section class="card card--front" aria-label="Business card front">
    <div class="front-accent" aria-hidden="true"></div>
    <div class="wordmark">VKM LTD</div>
  </section>

  <section class="card card--back" aria-label="Business card back">
    <div class="back-accent" aria-hidden="true"></div>
    <div class="wordmark">VKM LTD</div>
    <div class="holder">
      <p class="holder__name">Daniel Harper</p>
      <p class="holder__role">Manager</p>
    </div>
    <ul class="contact">
      <li class="contact__item">
        <svg class="contact__icon" viewBox="0 0 24 24"><path fill="#0d3a9c" d="M6.6 10.8a15 15 0 0 0 6.6 6.6l2.2-2.2a1 1 0 0 1 1-.25 11.4 11.4 0 0 0 3.6.57 1 1 0 0 1 1 1V20a1 1 0 0 1-1 1A17 17 0 0 1 3 4a1 1 0 0 1 1-1h3.5a1 1 0 0 1 1 1c0 1.25.2 2.45.57 3.57a1 1 0 0 1-.25 1z"/></svg>
        555-318-0472
      </li>
      <li class="contact__item">
        <svg class="contact__icon" viewBox="0 0 24 24"><rect x="2.5" y="5" width="19" height="14" rx="1.5" fill="none" stroke="#0d3a9c" stroke-width="2"/><path d="M3 6l9 7 9-7" fill="none" stroke="#0d3a9c" stroke-width="2"/></svg>
        hello@vkmltd.com
      </li>
      <li class="contact__item">
        <svg class="contact__icon" viewBox="0 0 24 24"><circle cx="12" cy="12" r="9.5" fill="none" stroke="#0d3a9c" stroke-width="2"/><path d="M2.5 12h19M12 2.5c3 3 3 16 0 19M12 2.5c-3 3-3 16 0 19" fill="none" stroke="#0d3a9c" stroke-width="1.6"/></svg>
        www.vkmltd.com
      </li>
      <li class="contact__address">48 Mill Road, Carver Bay, ZIP 4120</li>
    </ul>
  </section>
</body>
</html>
```